The quiet harbor with an elephant incorporated in the background

Target Market(s)

Real estate

Industry/Entity Type

Real Estate

Contact Information for Business Card

On back on want my name & number
In front I want the business name, "the quiet harbor", below to say staging & design

Logo Text

The quiet harbor

Font styles to use
Serif

Colors
000000

Requirements
Must have
• I want an elephant behind the writing in gold transperant

```html
<!DOCTYPE html>
<html lang="en">
<head>
<meta charset="utf-8">
<title>The Quiet Harbor – Business Cards</title>
<link href="https://fonts.googleapis.com/css2?family=EB+Garamond:wght@400;500;600&display=swap" rel="stylesheet">
<style>
  :root {
    --backdrop: #262626;
    --card-dark-top: #474747;
    --card-dark-bottom: #2f2f2f;
    --card-light: #fbfbfb;
    --ink-dark: #3c3c3c;
    --ink-muted: #6a6a6a;
    --ink-light: #e9e9e9;
    --rule-light: #d6d6d6;
    --gold-light: #f3d36a;
    --gold-mid: #c9a22e;
    --gold-deep: #7d5f16;
  }
  * { box-sizing: border-box; margin: 0; padding: 0; }
  html, body {
    width: 1200px; height: 997px; overflow: hidden;
    background: var(--backdrop);
    font-family: "EB Garamond", Georgia, serif;
  }
  .canvas { position: relative; width: 1200px; height: 997px; }

  .card {
    position: absolute;
    width: 540px; height: 320px;
    border-radius: 22px;
    box-shadow: 0 18px 40px rgba(0,0,0,0.55);
    overflow: hidden;
  }

  /* Back card */
  .card--back {
    left: 70px; top: 150px;
    background: linear-gradient(160deg, var(--card-dark-top), var(--card-dark-bottom));
    color: var(--ink-light);
  }
  .card--back .person-name {
    position: absolute; left: 150px; right: 30px; top: 48px;
    text-align: center;
    font-size: 30px; font-weight: 600; letter-spacing: 0.03em;
    text-transform: uppercase;
    line-height: 1.2;
  }
  .card--back .person-role {
    position: absolute; left: 120px; right: 20px; top: 92px;
    text-align: center;
    font-size: 15px; letter-spacing: 0.42em;
    line-height: 1.2;
  }
  .card--back .rule {
    position: absolute; left: 170px; width: 340px; height: 2px;
    background: var(--rule-light);
  }
  .card--back .rule--top { top: 138px; }
  .card--back .rule--bottom { top: 268px; }
  .card--back .mini-mark {
    position: absolute; left: 56px; top: 188px;
    width: 96px; height: 72px;
    background: radial-gradient(closest-side, var(--gold-mid) 0%, var(--gold-deep) 60%, rgba(125,95,22,0) 100%);
    opacity: 0.85;
  }
  .card--back .contact {
    position: absolute; left: 170px; width: 340px;
    text-align: center; font-size: 19px; line-height: 1.2;
  }
  .card--back .contact--phone { top: 168px; display: flex; justify-content: center; align-items: center; gap: 10px; }
  .card--back .contact--email { top: 224px; font-size: 18px; }
  .phone-icon { width: 24px; height: 24px; }

  /* Front card */
  .card--front {
    left: 590px; top: 527px;
    background: var(--card-light);
  }
  .card--front .brand-name {
    position: absolute; left: 0; right: 0; top: 58px;
    text-align: center;
    font-size: 34px; font-weight: 500; color: var(--ink-dark);
    text-transform: uppercase; letter-spacing: 0.02em;
    line-height: 1.2;
  }
  .card--front .brand-tagline {
    position: absolute; left: 0; right: 0; top: 102px;
    text-align: center;
    font-size: 14px; color: var(--ink-muted);
    text-transform: uppercase; letter-spacing: 0.55em;
    line-height: 1.2;
  }
  .card--front .elephant-art {
    position: absolute; left: 140px; top: 136px;
    width: 280px; height: 170px;
    background: radial-gradient(closest-side, var(--gold-light) 0%, var(--gold-mid) 55%, rgba(201,162,46,0) 100%);
  }
</style>
</head>
<body>
  <main class="canvas">
    <section class="card card--back">
      <h2 class="person-name">Claire Donovan</h2>
      <p class="person-role">Design &amp; Staging Consultant</p>
      <div class="rule rule--top"></div>
      <div class="mini-mark" role="img" aria-label="Small gold elephant figure"></div>
      <p class="contact contact--phone">
        <svg class="phone-icon" viewBox="0 0 24 24" aria-hidden="true">
          <circle cx="12" cy="12" r="12" fill="#e9e9e9"/>
          <rect x="8" y="5" width="8" height="14" rx="1.5" fill="none" stroke="#3a3a3a" stroke-width="1.5"/>
          <circle cx="12" cy="16.5" r="0.9" fill="#3a3a3a"/>
        </svg>
        <span>555-014-2736</span>
      </p>
      <p class="contact contact--email">clairedonovan@quietharbordesigns.com</p>
      <div class="rule rule--bottom"></div>
    </section>

    <section class="card card--front">
      <h1 class="brand-name">The Quiet Harbor</h1>
      <p class="brand-tagline">Staging &amp; Design</p>
      <div class="elephant-art" role="img" aria-label="Gold elephant figure with raised trunk"></div>
    </section>
  </main>
</body>
</html>
```